Gymnastics and fitness web design

Valdrey Gymnastics and fitness centre is opening a new branch in the United States.
Target Audience:
22 to 40 year old people who are not satisfied with their current body figure, shape and size.
and
Our programs
VoltaRig, Sports performance and personal training
DESIGN STYLE:
We want the site to be trendy, edgy and cool. The colors we prefer are blue, black and silver. Th idea is people should get motivated by seeing our website. We don't like adding many text in the design, images oriented design is what we are after.
Contents should be added-
Slider
who we are?
section for our programs
Why us?
Video showing some tutorials
Articles
contact us form with map, Address, Phone number, timings, and social media buttons.

```html
<!DOCTYPE html>
<html lang="en">
<head>
<meta charset="utf-8">
<title>Valdrey Gymnastics and fitness centre</title>
<link href="https://fonts.googleapis.com/css2?family=Open+Sans:wght@400;600;700&display=swap" rel="stylesheet">
<style>
:root{
  --cyan:#1a9cc4;
  --cyan-bright:#22b0dc;
  --ink:#1c1c1c;
  --dark:#121212;
  --dark-2:#1d1d1d;
  --grey:#6d6d6d;
  --light-grey:#a8a8a8;
  --white:#ffffff;
}
*{box-sizing:border-box;margin:0;padding:0}
html,body{width:1200px;height:4737px;overflow:hidden}
body{position:relative;font-family:"Open Sans",Arial,sans-serif;color:var(--ink);background:var(--white)}
.abs{position:absolute}
.btn{position:absolute;background:var(--cyan);color:var(--white);font-size:19px;display:flex;align-items:center;justify-content:center;text-transform:uppercase}
.section-title{position:absolute;left:0;width:1200px;text-align:center;font-size:44px;font-weight:400;letter-spacing:1px}
.section-title b{color:var(--cyan);font-weight:600}
.lead{position:absolute;left:220px;width:760px;text-align:center;font-size:15px;line-height:24px}
.photo{position:absolute}

/* header */
.site-header{position:absolute;left:0;top:0;width:1200px;height:114px;background:var(--white)}
.brand{position:absolute;left:82px;top:16px;color:var(--cyan)}
.brand-name{font-size:50px;line-height:52px;font-weight:400;letter-spacing:1px}
.brand-sub{font-size:17px;color:var(--ink);margin-top:2px}
.nav a{position:absolute;top:35px;height:53px;display:flex;align-items:center;font-size:17px;color:var(--ink);text-decoration:none}
.nav a.active{background:var(--cyan);color:var(--white);width:85px;left:385px;justify-content:center}

/* hero */
.hero{position:absolute;left:0;top:114px;width:1200px;height:565px;background:linear-gradient(90deg,#1a2a33 0%,#2b3b44 45%,#1a1f24 100%)}
.hero-text{position:absolute;left:82px;color:var(--white);line-height:1}
.hero-small{font-size:34px}
.hero-big{font-size:70px;font-weight:700;color:var(--cyan-bright)}
.hero-circle{position:absolute;left:622px;top:113px;width:430px;height:430px;border-radius:50%;background:radial-gradient(circle at 60% 40%,#e9e4dc,#b49c84 75%)}
.arrow{position:absolute;top:290px}

/* welcome */
.welcome-frame{position:absolute;left:76px;top:748px;width:467px;height:331px;border-left:10px solid var(--cyan);border-bottom:10px solid var(--cyan)}
.welcome-photo{left:88px;top:748px;width:455px;height:313px;background:linear-gradient(135deg,#6c6c6c,#2d2d2d 60%,#9a9a9a)}
.welcome-title{position:absolute;left:572px;top:762px;font-size:44px}
.welcome-title b{color:var(--cyan);font-weight:600}
.body-copy{position:absolute;font-size:13px;line-height:24px;color:var(--grey)}

/* programs */
.programs{position:absolute;left:0;top:1127px;width:1200px;height:648px;background:linear-gradient(90deg,#0d0d0d,#242424 60%,#151515)}
.program-photo{top:1270px;width:335px;height:227px}
.program-name{position:absolute;top:1528px;width:335px;text-align:center;color:var(--cyan-bright);font-size:20px;text-transform:uppercase}
.program-copy{position:absolute;top:1562px;width:335px;text-align:center;color:#cfcfcf;font-size:15px;line-height:23px}

/* tutorials */
.video{left:79px;top:1961px;width:628px;height:370px;background:linear-gradient(135deg,#cfcfcf,#7e7e7e 55%,#494949);border:4px solid #222}
.video-brand{position:absolute;left:96px;top:1970px;color:var(--cyan);font-size:40px}
.video-brand small{display:block;font-size:13px;color:#333;margin-top:-4px}
.video-bar{position:absolute;left:83px;top:2303px;width:620px;height:24px;background:#111}
.video-icon{position:absolute;left:654px;width:38px;height:34px;background:#333;border:1px solid #555}
.tut-item{position:absolute;left:736px;width:385px;height:111px}
.tut-thumb{position:absolute;left:0;top:0;width:145px;height:111px;background:linear-gradient(135deg,#5c5c5c,#b6b6b6)}
.tut-text{position:absolute;left:158px;top:2px;width:210px;font-size:18px;line-height:29px}
.tut-time{position:absolute;left:158px;top:72px;font-size:16px;color:var(--cyan);display:flex;align-items:center;gap:8px}
.tut-scroll{position:absolute;left:1116px;top:2060px;width:5px;height:160px;background:var(--cyan)}

/* why us */
.why{position:absolute;left:0;top:2394px;width:1200px;height:407px;background:linear-gradient(90deg,#1c1c1c 0%,#2e2a25 40%,#221f1c 100%)}
.why-photo{left:80px;top:2394px;width:330px;height:407px;background:linear-gradient(90deg,#2a2a2a,#6a5e52 60%,#2e2a25)}
.why-title{position:absolute;left:499px;top:2452px;font-size:44px;color:var(--white)}
.why-title b{color:var(--cyan-bright);font-weight:600}
.why-copy{position:absolute;left:499px;width:620px;font-size:13px;line-height:21px;color:#8f8f8f}

/* articles */
.cover{top:2987px;width:322px;height:364px}

/* contact */
.contact{position:absolute;left:0;top:3496px;width:1200px;height:489px;background:linear-gradient(180deg,#1596c2 0%,#1a8db6 55%,#15637f 100%)}
.field{position:absolute;background:var(--white);border:1px solid #ccc;font-size:14px;color:#777;padding:8px 10px}
.submit{position:absolute;left:521px;top:3865px;width:155px;height:54px;border:2px solid var(--white);border-radius:6px;color:var(--white);font-size:18px;display:flex;align-items:center;justify-content:center}

/* footer */
.footer{position:absolute;left:0;top:3985px;width:1200px;height:695px;background:linear-gradient(180deg,#151515,#202020 50%,#141414)}
.footer-brand{position:absolute;left:0;top:4030px;width:1200px;text-align:center;color:var(--cyan-bright);font-size:60px;line-height:62px}
.footer-sub{position:absolute;left:0;top:4094px;width:1200px;text-align:center;color:var(--cyan-bright);font-size:22px}
.social{position:absolute;top:4207px;width:50px;height:50px;border-radius:50%;background:var(--cyan)}
.map{left:79px;top:4333px;width:332px;height:136px;background:linear-gradient(135deg,#ecebe6,#d9d6cc)}
.foot-head{position:absolute;top:4330px;font-size:18px;color:var(--cyan-bright);font-weight:600;text-transform:uppercase}
.hours{position:absolute;left:436px;top:4370px;width:334px}
.hours div{display:flex;justify-content:space-between;font-size:14px;line-height:29.5px;color:#ddd;border-bottom:1px dotted #444}
.foot-tut{position:absolute;left:793px;width:330px;height:60px}
.foot-tut .tut-thumb{width:120px;height:60px}
.foot-tut p{position:absolute;left:130px;top:-2px;font-size:14px;line-height:20px;color:#ddd;width:200px}
.foot-tut span{position:absolute;left:130px;top:40px;font-size:14px;color:var(--cyan-bright)}
.contact-line{position:absolute;left:79px;font-size:14px;color:#ddd;display:flex;gap:10px;align-items:flex-start;line-height:22px}
.copyright{position:absolute;left:0;top:4680px;width:1200px;height:57px;background:#0e0e0e;color:var(--cyan-bright);font-size:14px;display:flex;align-items:center;justify-content:center}
.copyright span{color:#ddd;margin-left:6px}
</style>
</head>
<body>

<header class="site-header">
  <div class="brand"><div class="brand-name">VALDREY</div><div class="brand-sub">Gymnastics and fitness centre</div></div>
  <nav class="nav">
    <a class="active">HOME</a>
    <a style="left:496px">ABOUT</a>
    <a style="left:578px">OUR PROGRAMS</a>
    <a style="left:733px">WHY US?</a>
    <a style="left:834px">TUTORIALS</a>
    <a style="left:944px">ARTICLES</a>
    <a style="left:1048px">CONTACT</a>
  </nav>
</header>

<section class="hero" role="img" aria-label="Dark background photo of an athlete training">
  <div class="hero-text" style="top:175px">
    <div class="hero-small">TAKE CARE OF</div>
    <div class="hero-big" style="margin-top:8px">YOUR BODY</div>
    <div class="hero-small" style="margin-top:12px">IT'S THE ONLY PLACE YOU HAVE</div>
    <div class="hero-big" style="margin-top:8px">TO LIVE IN.</div>
  </div>
  <div class="hero-circle" role="img" aria-label="Woman exercising with a hula hoop, beside a measuring tape around a waist"></div>
  <svg class="arrow" style="left:30px" width="20" height="44"><path d="M16 2 L4 22 L16 42" stroke="#fff" stroke-width="2" fill="none"/></svg>
  <svg class="arrow" style="left:1150px" width="20" height="44"><path d="M4 2 L16 22 L4 42" stroke="#fff" stroke-width="2" fill="none"/></svg>
</section>

<section class="welcome">
  <div class="welcome-frame"></div>
  <div class="photo welcome-photo" role="img" aria-label="Athlete doing a one-arm plank push-up with a trainer"></div>
  <h2 class="welcome-title" style="font-weight:400">WELCOME TO <b>VALDREY</b></h2>
  <p class="body-copy" style="left:572px;top:824px;width:540px">Lorem Ipsum is simply dummy text of the printing and typesetting industry. Lorem Ipsum has been the industry's standard dummy text ever since the.</p>
  <p class="body-copy" style="left:572px;top:886px;width:540px">Lorem Ipsum is simply dummy text of the printing and typesetting industry. Lorem Ipsum has been the industry's standard dummy text ever since the 1500s, when an unknown printer took a galley of type and scrambled it to make a type.</p>
  <div class="btn" style="left:575px;top:985px;width:167px;height:57px">KNOW MORE</div>
</section>

<section class="programs" role="img" aria-label="Dark background photo of an athlete"></section>
<h2 class="section-title" style="top:1178px;color:#fff">OUR <b>PROGRAMS</b></h2>
<div class="photo program-photo" style="left:79px;background:linear-gradient(135deg,#1b2630,#4a5866)" role="img" aria-label="Two athletes lifting dumbbells"></div>
<div class="photo program-photo" style="left:433px;background:linear-gradient(135deg,#1f2e3a,#5c7b8c)" role="img" aria-label="Sprinter bursting from the start with dust"></div>
<div class="photo program-photo" style="left:786px;background:linear-gradient(135deg,#6a5a4c,#c7b9a6)" role="img" aria-label="Group doing sit-ups in a studio"></div>
<div class="program-name" style="left:79px">VoltaRig</div>
<div class="program-name" style="left:433px">Sports Performance</div>
<div class="program-name" style="left:786px">Personal Training</div>
<p class="program-copy" style="left:79px">Lorem Ipsum is simply dummy text of the printing and typesetting industry. Lorem Ipsum has been the industry's standard dummy text.</p>
<p class="program-copy" style="left:433px">Lorem Ipsum is simply dummy text of the printing and typesetting industry. Lorem Ipsum has been the industry's standard dummy text.</p>
<p class="program-copy" style="left:786px">Lorem Ipsum is simply dummy text of the printing and typesetting industry. Lorem Ipsum has been the industry's standard dummy text.</p>
<div class="btn" style="left:161px;top:1648px;width:167px;height:57px">KNOW MORE</div>
<div class="btn" style="left:516px;top:1648px;width:167px;height:57px">KNOW MORE</div>
<div class="btn" style="left:870px;top:1648px;width:167px;height:57px">KNOW MORE</div>

<section class="tutorials">
  <h2 class="section-title" style="top:1822px">OUR <b>TUTORIALS</b></h2>
  <p class="lead" style="top:1893px">Lorem Ipsum is simply dummy text of the printing and typesetting industry Lorem Ipsum has been the industry's standard dummy text ever since the is simply dummy text of the.</p>
  <div class="photo video" role="img" aria-label="Video still of a group fitness class stretching"></div>
  <div class="video-brand">VALDREY<small>Gymnastics and fitness centre</small></div>
  <div class="video-icon" style="top:1972px"></div>
  <div class="video-icon" style="top:2012px"></div>
  <div class="video-icon" style="top:2052px"></div>
  <div class="video-bar"></div>
  <svg class="abs" style="left:92px;top:2308px" width="60" height="14"><rect x="0" y="1" width="3" height="12" fill="#fff"/><rect x="6" y="1" width="3" height="12" fill="#fff"/><circle cx="40" cy="7" r="4" fill="#fff"/></svg>

  <div class="tut-item" style="top:1961px"><div class="tut-thumb" role="img" aria-label="Boxer training"></div><div class="tut-text">Lorem Ipsum is simply dummy text of the.</div><div class="tut-time"><svg width="16" height="16"><circle cx="8" cy="8" r="6.5" stroke="#1a9cc4" stroke-width="2" fill="none"/><path d="M8 4v4h3" stroke="#1a9cc4" stroke-width="1.6" fill="none"/></svg>12:13 pm</div></div>
  <div class="tut-item" style="top:2091px"><div class="tut-thumb" role="img" aria-label="Group workout class"></div><div class="tut-text">Lorem Ipsum is simply dummy text of the.</div><div class="tut-time"><svg width="16" height="16"><circle cx="8" cy="8" r="6.5" stroke="#1a9cc4" stroke-width="2" fill="none"/><path d="M8 4v4h3" stroke="#1a9cc4" stroke-width="1.6" fill="none"/></svg>2:23 pm</div></div>
  <div class="tut-item" style="top:2220px"><div class="tut-thumb" role="img" aria-label="Athlete on a bench press"></div><div class="tut-text">Lorem Ipsum is simply dummy text of the.</div><div class="tut-time"><svg width="16" height="16"><circle cx="8" cy="8" r="6.5" stroke="#1a9cc4" stroke-width="2" fill="none"/><path d="M8 4v4h3" stroke="#1a9cc4" stroke-width="1.6" fill="none"/></svg>5:40 pm</div></div>
  <div class="tut-scroll"></div>
</section>

<section class="why" role="img" aria-label="Dark background"></section>
<div class="photo why-photo" role="img" aria-label="Woman in sports wear posing in low light"></div>
<h2 class="why-title" style="font-weight:400">WHY <b>US ?</b></h2>
<p class="why-copy" style="top:2516px">Lorem Ipsum is simply dummy text of the printing and typesetting industry. Lorem Ipsum has been the industry's standard dummy text ever since the 1500s, when an unknown.</p>
<p class="why-copy" style="top:2580px">Lorem Ipsum is simply dummy text of the printing and typesetting industry. Lorem Ipsum has been the industry's standard dummy text ever since the 1500s, when an unknown printer took a galley of type and scrambled it to make a type.</p>
<div class="btn" style="left:502px;top:2690px;width:167px;height:54px">CONTACT US</div>

<section class="articles">
  <h2 class="section-title" style="top:2852px">OUR <b>ARTICLES</b></h2>
  <p class="lead" style="top:2918px">Lorem Ipsum is simply dummy text of the printing and typesetting industry Lorem Ipsum has been the industry's standard dummy text ever since the is simply dummy text of the.</p>
  <div class="photo cover" style="left:79px;background:linear-gradient(180deg,#dfe6ea,#9aa4aa)" role="img" aria-label="Fitness magazine cover with a man crouching"></div>
  <div class="photo cover" style="left:439px;background:linear-gradient(180deg,#f1eee8,#c6b9a6)" role="img" aria-label="Training book cover with a woman lifting dumbbells"></div>
  <div class="photo cover" style="left:799px;background:linear-gradient(180deg,#3a3a3a,#6b5a44)" role="img" aria-label="Gymnastics coaching manual cover with a gymnast on rings"></div>
  <div class="btn" style="left:486px;top:3376px;width:228px;height:57px">VIEW ALL ARTICLES</div>
</section>

<section class="contact" role="img" aria-label="Blue tinted photo of a gym floor"></section>
<h2 class="section-title" style="top:3548px;color:#1c1c1c">CONTACT <b style="color:#fff">US</b></h2>
<p class="lead" style="top:3603px;color:#fff">Lorem Ipsum is simply dummy text of the printing and typesetting industry Lorem Ipsum has been the industry's standard dummy text ever since the is simply dummy text of the.</p>
<div class="field" style="left:152px;top:3682px;width:293px;height:48px">Name*</div>
<div class="field" style="left:458px;top:3682px;width:287px;height:48px">Email*</div>
<div class="field" style="left:758px;top:3682px;width:287px;height:48px">Phone*</div>
<div class="field" style="left:152px;top:3742px;width:893px;height:111px">Message*</div>
<div class="submit">SUBMIT</div>

<footer class="footer" role="img" aria-label="Dark cracked texture background"></footer>
<div class="footer-brand">VALDREY</div>
<div class="footer-sub">Gymnastics and fitness centre</div>
<p class="lead" style="top:4136px;color:#bbb">Lorem Ipsum is simply dummy text of the printing and typesetting industry Lorem Ipsum has been the industry's standard dummy text ever.</p>
<div class="social" style="left:480px" aria-label="Social link 1"></div>
<div class="social" style="left:543px" aria-label="Social link 2"></div>
<div class="social" style="left:607px" aria-label="Social link 3"></div>
<div class="social" style="left:667px" aria-label="Social link 4"></div>

<div class="photo map" role="img" aria-label="Street map marking the centre's location"></div>
<div class="contact-line" style="top:4495px"><svg width="16" height="22"><path d="M8 1a6 6 0 0 1 6 6c0 5-6 13-6 13S2 12 2 7a6 6 0 0 1 6-6z" fill="#1a9cc4"/><circle cx="8" cy="7" r="2.2" fill="#141414"/></svg><div><b style="color:#fff;font-weight:600">VALDREY Gymnastics and fitness centre</b><br>Address, flat num , state, city,<br>pincode area.</div></div>
<div class="contact-line" style="top:4590px"><svg width="16" height="18"><path d="M3 2h4l1.5 4-2 1.5a10 10 0 0 0 4 4L12 9.5l4 1.5v4a2 2 0 0 1-2 2A13 13 0 0 1 1 4a2 2 0 0 1 2-2z" fill="#1a9cc4"/></svg>+ (1) 0155 456 789</div>
<div class="contact-line" style="top:4618px"><svg width="16" height="14"><rect x="1" y="2" width="14" height="10" fill="none" stroke="#1a9cc4" stroke-width="1.6"/><path d="M1 2l7 6 7-6" fill="none" stroke="#1a9cc4" stroke-width="1.6"/></svg>info@valdrey.com</div>

<div class="foot-head" style="left:436px">Opening Hours</div>
<div class="hours">
  <div><span>Sunday</span><span>08:00 - 14:00</span></div>
  <div><span>Monday</span><span>08:00 - 14:00</span></div>
  <div><span>Tuesday</span><span>08:00 - 14:00</span></div>
  <div><span>Wednesday</span><span>08:00 - 14:00</span></div>
  <div><span>Thursday</span><span>08:00 - 14:00</span></div>
  <div><span>Friday</span><span>08:00 - 14:00</span></div>
  <div><span>Saturday</span><span>08:00 - 14:00</span></div>
  <div><span>Sunday</span><span>08:00 - 14:00</span></div>
</div>

<div class="foot-head" style="left:793px">Our Tutorials</div>
<div class="foot-tut" style="top:4370px"><div class="tut-thumb" role="img" aria-label="Athlete jumping"></div><p>Lorem Ipsum is simply dummy text of the.</p><span>12:13 pm</span></div>
<div class="foot-tut" style="top:4456px"><div class="tut-thumb" role="img" aria-label="Gymnast stretching"></div><p>Lorem Ipsum is simply dummy text of the.</p><span>12:13 pm</span></div>
<div class="foot-tut" style="top:4540px"><div class="tut-thumb" role="img" aria-label="Group training outdoors"></div><p>Lorem Ipsum is simply dummy text of the.</p><span>12:13 pm</span></div>

<div class="copyright">©VALDREY Gymnastics and fitness centre -<span>2017. All rights reserved</span></div>

</body>
</html>
```